Brightfen Business Card Redesign & Logo Update

We need to update our business cards to something more modern and fresh. Brightfen can provide the current color schemes and old design examples, but welcome creativity in helping us with this redesign. PLEASE NOTE that we no longer utilize the "tree" and/or "leaf" imagery in our branding. If able would apprecaite an update on the quality of our "words only" logo in Ai. / PNG formats too.

Target Market(s)

Investors, landowners, corporate partners, contractors

Industry/Entity Type

Environmental Restoration & Conservation

Contact Information for Business Card

Logo, persons name, title, mailing address, phone and email, website url

Font styles to use
Other font styles liked:
• Merriweather

Requirements
Nice to have
• Logo, persons name, title, mailing address, phone and email, website url, but open to ideams
Should not have
• No all back backgrounds

```html
<!DOCTYPE html>
<html lang="en">
<head>
<meta charset="utf-8">
<title>Brightfen Business Card</title>
<link href="https://fonts.googleapis.com/css2?family=Merriweather:wght@400;700;900&display=swap" rel="stylesheet">
<style>
  :root {
    --backdrop: #d3d4d6;
    --card: #ffffff;
    --green: #1b8741;
    --orange: #ef8a26;
    --ink: #1e1e1e;
    --rule: #2a2a2a;
  }
  * { margin: 0; padding: 0; box-sizing: border-box; }
  html, body {
    width: 900px;
    height: 1200px;
    overflow: hidden;
    background: var(--backdrop);
    font-family: "Merriweather", Georgia, serif;
    color: var(--ink);
  }
  .card {
    position: absolute;
    left: 120px;
    width: 660px;
    height: 379px;
    background: var(--card);
  }
  .card--front { top: 202px; }
  .card--back { top: 620px; }

  .wordmark {
    position: absolute;
    font-family: "Merriweather", Georgia, serif;
    font-weight: 900;
    color: var(--green);
    white-space: nowrap;
    transform: translate(-50%, -50%);
    letter-spacing: 0.5px;
  }
  .card--front .wordmark { left: 330px; top: 188px; font-size: 64px; }
  .card--back .wordmark { left: 178px; top: 186px; font-size: 44px; }

  .divider {
    position: absolute;
    left: 330px;
    top: 101px;
    width: 1.5px;
    height: 176px;
    background: var(--rule);
  }
  .contact {
    position: absolute;
    left: 355px;
    top: 96px;
    font-size: 16.5px;
    line-height: 1;
  }
  .contact__name {
    font-size: 26px;
    font-weight: 700;
    margin-bottom: 8px;
  }
  .contact__title {
    color: var(--orange);
    font-size: 16px;
    margin-bottom: 12px;
  }
  .contact__address { line-height: 24px; margin-bottom: 6px; }
  .contact__line {
    display: flex;
    align-items: center;
    height: 24px;
    letter-spacing: 0.5px;
  }
  .contact__line svg {
    width: 14px;
    height: 14px;
    margin-right: 6px;
    flex: none;
  }
  .social {
    position: absolute;
    left: 0;
    width: 660px;
    top: 313px;
    display: flex;
    justify-content: center;
    gap: 13px;
  }
  .social__dot {
    width: 32px;
    height: 32px;
    border-radius: 50%;
    background: var(--green);
  }
  .social__dot--alt { background: var(--orange); }
</style>
</head>
<body>
  <section class="card card--front">
    <div class="wordmark">Brightfen</div>
  </section>

  <section class="card card--back">
    <div class="wordmark">Brightfen</div>
    <div class="divider"></div>
    <div class="contact">
      <div class="contact__name">Dalton Reyes</div>
      <div class="contact__title">Director</div>
      <div class="contact__address">4820 County Road 318,<br>Marlow, TX 75990</div>
      <div class="contact__line">
        <svg viewBox="0 0 24 24" aria-hidden="true"><path fill="var(--green)" d="M6.6 10.8a15.1 15.1 0 0 0 6.6 6.6l2.2-2.2a1 1 0 0 1 1-.25 11.4 11.4 0 0 0 3.6.57 1 1 0 0 1 1 1V20a1 1 0 0 1-1 1A17 17 0 0 1 3 4a1 1 0 0 1 1-1h3.5a1 1 0 0 1 1 1c0 1.25.2 2.45.57 3.57a1 1 0 0 1-.25 1z"/></svg>
        (555) 214-8830
      </div>
      <div class="contact__line">
        <svg viewBox="0 0 24 24" aria-hidden="true"><path fill="var(--green)" d="M2 5h20v3l-10 6L2 8z"/><path fill="var(--green)" d="M2 10l10 6 10-6v9H2z"/></svg>
        info@brightfencredits.com
      </div>
      <div class="contact__line">
        <svg viewBox="0 0 24 24" aria-hidden="true"><circle cx="12" cy="12" r="9" fill="none" stroke="var(--green)" stroke-width="2"/><path d="M3 12h18M12 3c3 3 3 15 0 18M12 3c-3 3-3 15 0 18" fill="none" stroke="var(--green)" stroke-width="1.6"/></svg>
        www.brightfencredits.com
      </div>
    </div>
    <div class="social">
      <div class="social__dot"></div>
      <div class="social__dot social__dot--alt"></div>
      <div class="social__dot"></div>
    </div>
  </section>
</body>
</html>
```